Fernhollow Architectural Systems Business Card

We have a logo - but we need a business card. We are a specialty manufacturer of wood wall and ceiling panels. Please visit our website - www.fernhollowpanels.com to see examples of our products.
We create wood architectural systems - so we would love to see wood on the card somehow. Maybe something similar to our grille system?
We would like a spot on the business card for a QR code that people can scan to add the contact to their phone (we have the QR codes - just need a spot on the card).
As for the contact info - we want to keep it simple. (Name, Cell phone, Fax, email, website)

Target Market(s)

Architects and general contractors

Industry/Entity Type

Construction

Contact Information for Business Card

Name, Cell phone, fax, email, website

Requirements
Must have
• space for a QR code, wood feature
Nice to have
• We just want something a little different - but not too crazy. We want to stand out - but in a professional way.
Should not have
• nothing too busy

```html
<!DOCTYPE html>
<html lang="en">
<head>
<meta charset="utf-8">
<title>Fernhollow Architectural Systems – Business Card</title>
<link href="https://fonts.googleapis.com/css2?family=Open+Sans:wght@300;400;700;800&display=swap" rel="stylesheet">
<style>
  :root {
    --brand-red: #b20000;
    --ink: #1a1a1a;
    --backdrop: #2d2c2d;
    --card-white: #ffffff;
    --wood-light: #e9c596;
    --wood-mid: #dcae73;
    --wood-deep: #d09a5a;
  }
  * { margin: 0; padding: 0; box-sizing: border-box; }
  html, body { width: 887px; height: 1200px; overflow: hidden; }
  body {
    position: relative;
    background: var(--backdrop);
    font-family: "Open Sans", Arial, sans-serif;
  }

  /* ---------- Front ---------- */
  .card-front {
    position: absolute; left: 0; top: 0;
    width: 887px; height: 574px;
    border-radius: 43px;
    overflow: hidden;
  }
  .wood-panel {
    position: absolute; left: 0; top: 0;
    width: 100%; height: 541px;
    background: linear-gradient(90deg, var(--wood-light) 0%, var(--wood-mid) 30%, var(--wood-light) 55%, var(--wood-deep) 80%, var(--wood-light) 100%);
  }
  .front-brand {
    position: absolute; left: 161px; top: 190px;
    display: flex; align-items: center; gap: 22px;
    color: var(--brand-red);
    font-weight: 800;
  }
  .brand-dot {
    width: 140px; height: 140px; border-radius: 50%;
    background: var(--brand-red);
    flex: none;
  }
  .brand-name { line-height: 1; text-transform: uppercase; }
  .front-brand .brand-main { display: block; font-size: 54px; letter-spacing: 0; }
  .front-brand .brand-sub { display: block; font-size: 27px; letter-spacing: 6px; margin-top: 8px; }
  .url-band {
    position: absolute; left: 0; top: 541px;
    width: 100%; height: 33px;
    background: var(--brand-red);
    color: #fff;
    font-size: 21px; font-weight: 400;
    text-align: center; line-height: 33px;
    letter-spacing: 0.5px;
  }

  /* ---------- Back ---------- */
  .card-back {
    position: absolute; left: 0; top: 626px;
    width: 887px; height: 574px;
    background: var(--card-white);
    border-radius: 43px 43px 0 0;
  }
  .back-brand {
    position: absolute; left: 56px; top: 140px;
    display: flex; align-items: center; gap: 12px;
    color: var(--brand-red);
    font-weight: 800;
  }
  .back-brand .brand-dot { width: 88px; height: 88px; }
  .back-brand .brand-main { display: block; font-size: 31px; }
  .back-brand .brand-sub { display: block; font-size: 15px; letter-spacing: 3px; margin-top: 5px; }
  .qr-spot {
    position: absolute; left: 166px; top: 308px;
    width: 128px; height: 127px;
    border: 2.5px solid var(--brand-red);
  }
  .divider {
    position: absolute; left: 442px; top: 116px;
    width: 2px; height: 341px;
    background: var(--brand-red);
  }
  .person-name {
    position: absolute; left: 499px; top: 146px;
    font-size: 38px; color: var(--brand-red);
    line-height: 1;
    letter-spacing: 0.5px;
  }
  .person-name .first { font-weight: 700; }
  .person-name .last { font-weight: 300; }
  .contact-list { list-style: none; position: absolute; left: 499px; top: 225px; }
  .contact-item {
    display: flex; align-items: center;
    height: 34px; margin-bottom: 23px;
    font-size: 19px; color: var(--ink); font-weight: 400;
  }
  .contact-item svg { width: 34px; height: 34px; flex: none; margin-right: 12px; fill: var(--brand-red); }
</style>
</head>
<body>

<section class="card-front">
  <div class="wood-panel" role="img" aria-label="Photograph of light pine wood wall panels with vertical boards"></div>
  <div class="front-brand">
    <span class="brand-dot"></span>
    <span class="brand-name">
      <span class="brand-main">Fernhollow</span>
      <span class="brand-sub">Architectural Systems</span>
    </span>
  </div>
  <div class="url-band">www.fernhollowpanels.com</div>
</section>

<section class="card-back">
  <div class="back-brand">
    <span class="brand-dot"></span>
    <span class="brand-name">
      <span class="brand-main">FERNHOLLOW</span>
      <span class="brand-sub">ARCHITECTURAL SYSTEMS</span>
    </span>
  </div>
  <div class="qr-spot" aria-label="Space for contact QR code"></div>
  <div class="divider"></div>

  <h1 class="person-name"><span class="first">NAME</span> <span class="last">HERE</span></h1>
  <ul class="contact-list">
    <li class="contact-item">
      <svg viewBox="0 0 34 34" aria-hidden="true"><path d="M7 2c2 0 3 1 4 3l2 5c.6 1.5 0 2.6-1 3.5l-2 1.6c1.8 3.8 4.6 6.6 8.4 8.4l1.6-2c.9-1 2-1.6 3.5-1l5 2c2 1 3 2 3 4 0 3-3 6-6 6C13 32 2 21 2 8c0-3 3-6 5-6z"/></svg>
      +0123-456-789
    </li>
    <li class="contact-item">
      <svg viewBox="0 0 34 34" aria-hidden="true"><rect x="9" y="1" width="16" height="8"/><rect x="1" y="10" width="32" height="15" rx="2"/><rect x="7" y="20" width="20" height="13" fill="#fff" stroke="#b20000" stroke-width="2"/><rect x="10" y="24" width="14" height="1.5"/><rect x="10" y="28" width="14" height="1.5"/></svg>
      +0123-456-789
    </li>
    <li class="contact-item">
      <svg viewBox="0 0 34 34" aria-hidden="true"><text x="17" y="27" text-anchor="middle" font-family="Open Sans, sans-serif" font-weight="700" font-size="34" fill="#b20000">@</text></svg>
      name@fernhollowpanels.com
    </li>
    <li class="contact-item">
      <svg viewBox="0 0 34 34" aria-hidden="true"><circle cx="17" cy="17" r="16"/><g fill="none" stroke="#fff" stroke-width="1.6"><ellipse cx="17" cy="17" rx="7" ry="16"/><line x1="17" y1="1" x2="17" y2="33"/><line x1="1" y1="17" x2="33" y2="17"/><path d="M4 9h26M4 25h26"/></g></svg>
      www.fernhollowpanels.com
    </li>
  </ul>
</section>

</body>
</html>
```